Pediatric Therapy Clinic Brochure

We need a Brochure for a new pediatric therapy clinic. The clinic offers occupational therapy, physical therapy, speech therapy and feeding therapy. We want a brochure for parents, doctors and medical professional. It should have a fun and inviting, but still professional feel. Should be kid focused, bright and colorful. All the text / wording is there and a rough layout. Now I need someone to tidy and jazz it up and make it look professional.

Target Market(s)

Parents, doctors, medical professional

Industry/Entity Type

Medical

Font styles to use
Serif
Sans Serif

Requirements
Must have
• Keep All the text with information about services the same. Logo on front. Pictures throughout (use any of the pictures provided) (try and match up with corresponding service) (pictures are labeled). Need to have Map and contact info
• Keep colors consistent with our logo
Nice to have
• Background, special effects. Make it look fancy and professional
Should not have
• Not so busy that is takes away from the text

```html
<!DOCTYPE html>
<html lang="en">
<head>
<meta charset="utf-8">
<title>Brightpath Pediatric Therapy – Inside Spread</title>
<link rel="stylesheet" href="https://fonts.googleapis.com/css2?family=Oswald:wght@600;700&family=Arimo:wght@400;700&display=swap">
<style>
  :root {
    --page-bg: #9a9a9c;
    --sky: #d6e7ef;
    --sky-light: #eef5f8;
    --blue: #1b57a5;
    --orange: #e4611b;
    --lime: #b7d031;
    --lime-dark: #a2bd22;
    --text-blue: #2a5f9e;
  }
  * { box-sizing: border-box; margin: 0; padding: 0; }
  html, body { width: 1200px; height: 1200px; overflow: hidden; }
  body {
    background: var(--page-bg);
    font-family: "Arimo", Arial, sans-serif;
    position: relative;
  }
  .spread {
    position: absolute;
    left: 30px; top: 160px;
    width: 1140px; height: 880px;
    background: linear-gradient(180deg, var(--sky-light) 0%, var(--sky) 100%);
    overflow: hidden;
    box-shadow: 0 18px 40px rgba(0,0,0,.25);
  }
  .spread-backdrop { position: absolute; inset: 0; width: 100%; height: 100%; }
  .panels { position: absolute; inset: 0; display: flex; }
  .panel {
    width: 380px; height: 880px; position: relative;
    padding: 0 34px; display: flex; flex-direction: column;
  }
  .panel + .panel { border-left: 1px solid rgba(120,150,170,.25); }

  .service-title {
    font-family: "Oswald", "Arial Narrow", sans-serif;
    font-weight: 700; color: var(--blue);
    font-size: 30px; line-height: 1; text-align: center;
    letter-spacing: -.3px;
  }
  .service-intro {
    font-size: 13.5px; line-height: 1.3; color: var(--text-blue);
    text-align: center; margin-top: 6px;
  }
  .service-rule { height: 3px; background: var(--blue); margin: 8px 0 12px; border-radius: 2px; }
  .service-list { list-style: none; }
  .service-list li {
    position: relative; padding-left: 14px;
    font-weight: 700; font-size: 13.5px; line-height: 1.32;
    color: var(--orange);
  }
  .service-list li::before { content: "•"; position: absolute; left: 0; }

  .photo { border-radius: 2px; }
  .photo-hero {
    height: 250px; margin: 24px -14px 22px;
    background: radial-gradient(ellipse at 50% 45%, #f2c9a8 0%, #e9a47c 30%, #d9433d 55%, #f3f3f1 75%);
  }
  .photo-row { position: absolute; left: 24px; right: 24px; bottom: 22px; display: flex; gap: 16px; }
  .photo-small { flex: 1; height: 160px; border: 6px solid #fff; }
  .photo-meal { background: linear-gradient(160deg, #f4eee6, #e2a060 55%, #c9582c); }
  .photo-ball { background: linear-gradient(170deg, #f5f2ee 0%, #e9c6a8 35%, #c0332c 62%, #2346a8 100%); }

  .block-speech { margin-top: 44px; }
  .block-sensory { margin-top: 26px; }
  .block-feeding { margin-top: 44px; }
  .block-physical { margin-top: 26px; }
  .block-group { margin-top: 40px; }

  .brand {
    position: absolute; left: 0; right: 0; bottom: 46px;
    display: flex; align-items: center; justify-content: center; gap: 10px;
  }
  .brand-dot { width: 22px; height: 22px; border-radius: 50%; background: var(--orange); }
  .brand-name {
    font-family: "Oswald", "Arial Narrow", sans-serif; font-weight: 700;
    font-size: 30px; color: var(--blue); line-height: 1; text-align: center;
  }
  .brand-name small { display: block; font-size: 16px; letter-spacing: 1.5px; }

  .group-note {
    margin-top: 22px; text-align: center;
    color: var(--orange); font-size: 14px;
  }
</style>
</head>
<body>
<main class="spread">
  <svg class="spread-backdrop" viewBox="0 0 1140 880" preserveAspectRatio="none" aria-hidden="true">
    <ellipse cx="200" cy="470" rx="210" ry="110" fill="#ffffff" opacity=".35"/>
    <ellipse cx="610" cy="300" rx="190" ry="150" fill="#ffffff" opacity=".3"/>
    <ellipse cx="930" cy="240" rx="230" ry="130" fill="#ffffff" opacity=".3"/>
    <ellipse cx="640" cy="640" rx="170" ry="120" fill="#ffffff" opacity=".3"/>
    <path d="M0,615 C130,580 280,578 380,598 C520,625 640,735 760,718 C840,575 1000,548 1140,560 L1140,880 L0,880 Z" fill="var(--lime)"/>
    <path d="M380,598 C520,625 640,735 760,718 L760,880 L380,880 Z" fill="var(--lime-dark)" opacity=".25"/>
  </svg>

  <div class="panels">
    <section class="panel panel-occupational">
      <div class="photo photo-hero" role="img" aria-label="Photo of a smiling child with paint-covered hands"></div>
      <h2 class="service-title">OCCUPATIONAL THERAPY</h2>
      <p class="service-intro">Helping children build better self-esteem, confidence and independence in all the things they do.</p>
      <div class="service-rule"></div>
      <ul class="service-list">
        <li>Sensory Processing Disorder</li>
        <li>Balance, Coordination, Strength, and Endurance</li>
        <li>Fine Motor and Handwriting</li>
        <li>Visual- Motor Integration</li>
        <li>Play and Social Skills</li>
        <li>Feeding and Oral Motor Skills</li>
        <li>Self-Care</li>
        <li>Academic and Cognitive Skills</li>
        <li>Behavioral Difficulties</li>
        <li>Developmental Delays</li>
      </ul>
      <div class="photo-row">
        <div class="photo photo-small photo-meal" role="img" aria-label="Photo of a toddler playing with spaghetti at mealtime"></div>
        <div class="photo photo-small photo-ball" role="img" aria-label="Photo of a child leaning on a blue therapy ball"></div>
      </div>
    </section>

    <section class="panel panel-speech">
      <div class="block-speech">
        <h2 class="service-title">SPEECH THERAPY</h2>
        <p class="service-intro">Helping children speak, communicate and understand language.</p>
        <div class="service-rule"></div>
        <ul class="service-list">
          <li>Expressive and Receptive Language</li>
          <li>Speech and Language Developmental Milestones</li>
          <li>Articulation / Intelligibility</li>
          <li>Speech Fluency</li>
          <li>Pragmatics and Social Skills</li>
          <li>Literacy and Vocabulary</li>
          <li>Apraxia of Speech</li>
          <li>Augmentative and Alternative Communication</li>
          <li>Feeding and Oral Motor</li>
        </ul>
      </div>
      <div class="block-sensory">
        <h2 class="service-title">SENSORY INTEGRATION</h2>
        <p class="service-intro">Gradually increasing play based activities to improve a child's nervous system. Helping children learn to self-regulate their emotions, behaviors and arousal levels.</p>
        <div class="service-rule"></div>
        <ul class="service-list">
          <li>Autism and ADHD</li>
          <li>Sensory Processing Disorder</li>
          <li>Poor Tolerance of Sensory Stimuli from the Environment</li>
          <li>Meltdowns and Tantrums</li>
          <li>Poor Balance/Body Awareness</li>
          <li>Poor Attention and Concentration</li>
          <li>Poor Self-Regulation</li>
          <li>Behavior and Social Difficulties</li>
          <li>Poor Motor Coordination and Motor Planning</li>
          <li>Aggression, Frustration or Avoidance Behaviors</li>
        </ul>
      </div>
      <div class="brand">
        <span class="brand-dot"></span>
        <p class="brand-name">Brightpath<small>PEDIATRIC THERAPY</small></p>
      </div>
    </section>

    <section class="panel panel-physical">
      <div class="block-feeding">
        <h2 class="service-title">FEEDING THERAPY</h2>
        <p class="service-intro">Providing skilled assessment and intervention to children with feeding difficulties.</p>
        <div class="service-rule"></div>
        <ul class="service-list">
          <li>Food Aversions</li>
          <li>Food Refusal</li>
          <li>Very Picky Eating</li>
          <li>Avoidance of Certain Textures</li>
          <li>Gagging and Vomiting</li>
          <li>Oral Motor/ Chewing Difficulties</li>
          <li>Limited Diet/Food Repertoire</li>
        </ul>
      </div>
      <div class="block-physical">
        <h2 class="service-title">PHYSICAL THERAPY</h2>
        <p class="service-intro">Helping children move and interact within their environment smoothly and confidently.</p>
        <div class="service-rule"></div>
        <ul class="service-list">
          <li>Torticollis</li>
          <li>Walking and Mobility</li>
          <li>Developmental Motor Milestones</li>
          <li>Balance, Coordination, Motor Planning</li>
          <li>Strength, Muscle Tone and Range of Motion</li>
          <li>Sports Injuries</li>
          <li>Toe Walking</li>
          <li>Myofascial Release</li>
          <li>Postural Control and Positioning</li>
        </ul>
      </div>
      <div class="block-group">
        <h2 class="service-title">GROUP THERAPY</h2>
        <p class="service-intro">Using peer role models to learn new and challenging skills.</p>
        <div class="service-rule"></div>
        <ul class="service-list">
          <li>Social Groups</li>
          <li>Feeding Groups</li>
        </ul>
        <p class="group-note">**More Group Classes Coming Soon</p>
      </div>
    </section>
  </div>
</main>
</body>
</html>
```